Upscale business cards needed for Board of Directors

We need professional business cards created for members of our family business Board of Directors. We would like these relatively simple and straightforward, but also with a unique element to set them apart. Probably stick with neutral and simple colors - white, grey etc. We need space for the traditional elements, including name, title, address, email/phone number. And we will be creating several from this template so it needs to be template that is easy to switch information in and out of.
Business
See description

```html
<!DOCTYPE html>
<html lang="en">
<head>
<meta charset="utf-8">
<title>Harbourline Holdings – Business Cards</title>
<link rel="stylesheet" href="https://fonts.googleapis.com/css2?family=Roboto:wght@300;400;700&display=swap">
<style>
  :root {
    --page: #ece9e3;
    --paper: #ffffff;
    --paper-shade: #f1f1f0;
    --tan: #bdb292;
    --tan-light: #cfc6a6;
    --tan-dark: #a99e7e;
    --ink: #2c2c2c;
    --on-tan: #ffffff;
    --rule: rgba(255,255,255,0.55);
  }
  * { box-sizing: border-box; margin: 0; padding: 0; }
  html, body { width: 1200px; height: 1023px; overflow: hidden; }
  body {
    background: var(--page);
    font-family: "Roboto", Arial, sans-serif;
    position: relative;
  }
  .card {
    position: absolute;
    width: 560px;
    height: 320px;
    border-radius: 18px;
    overflow: hidden;
    box-shadow: 0 10px 24px rgba(0,0,0,0.18);
  }
  .card-front {
    left: 70px; top: 110px;
    background: var(--paper);
  }
  .front-brand {
    position: absolute; left: 0; top: 0; right: 0; height: 175px;
    background: linear-gradient(180deg, var(--paper) 0%, var(--paper-shade) 100%);
    display: flex; flex-direction: column; justify-content: center;
    padding-left: 56px;
  }
  .brand-name {
    font-weight: 700;
    color: var(--ink);
    text-transform: uppercase;
    line-height: 1;
  }
  .front-brand .brand-name .line-1 { font-size: 56px; letter-spacing: 1px; display: block; }
  .front-brand .brand-name .line-2 { font-size: 28px; letter-spacing: 19px; display: block; margin-top: 8px; padding-left: 60px; }
  .front-details {
    position: absolute; left: 0; right: 0; bottom: 0; height: 145px;
    background: linear-gradient(160deg, var(--tan-light) 0%, var(--tan) 55%, var(--tan-dark) 100%);
    color: var(--on-tan);
    display: flex; align-items: center;
  }
  .person { width: 260px; padding-left: 56px; }
  .person-name { font-size: 26px; font-weight: 400; letter-spacing: 0.5px; }
  .person-title { font-size: 14px; font-weight: 300; margin-top: 4px; letter-spacing: 0.5px; }
  .divider { width: 1px; height: 96px; background: var(--rule); }
  .contact { list-style: none; padding-left: 32px; font-size: 13px; font-weight: 300; letter-spacing: 0.4px; }
  .contact li { display: flex; align-items: flex-start; gap: 8px; margin: 3px 0; }
  .contact svg { width: 12px; height: 12px; flex: none; margin-top: 2px; }
  .card-back {
    left: 570px; top: 590px;
    background: linear-gradient(150deg, var(--tan-light) 0%, var(--tan) 55%, var(--tan-dark) 100%);
    display: flex; align-items: center; justify-content: center;
  }
  .card-back .brand-name { color: var(--on-tan); text-align: left; }
  .card-back .brand-name .line-1 { font-size: 60px; letter-spacing: 1px; display: block; }
  .card-back .brand-name .line-2 { font-size: 30px; letter-spacing: 21px; display: block; margin-top: 10px; padding-left: 56px; }
</style>
</head>
<body>
  <section class="card card-front" aria-label="Business card front">
    <div class="front-brand">
      <p class="brand-name"><span class="line-1">Harbourline</span><span class="line-2">Holdings</span></p>
    </div>
    <div class="front-details">
      <div class="person">
        <p class="person-name">Your Name</p>
        <p class="person-title">Title</p>
      </div>
      <div class="divider"></div>
      <ul class="contact">
        <li>
          <svg viewBox="0 0 12 12" fill="none" stroke="currentColor" stroke-width="1"><circle cx="6" cy="6" r="5"/><path d="M4.3 3.6c-.4.6 0 2 1 3s2.4 1.4 3 1l-.6-1-.9.3-1.6-1.6.3-.9z" fill="currentColor" stroke="none"/></svg>
          <span>00-000-00000</span>
        </li>
        <li>
          <svg viewBox="0 0 12 12" fill="none" stroke="currentColor" stroke-width="1"><rect x="1" y="2.5" width="10" height="7"/><path d="M1 2.5l5 4 5-4"/></svg>
          <span>info@example.com</span>
        </li>
        <li>
          <svg viewBox="0 0 12 12" fill="currentColor"><path d="M6 1a3.5 3.5 0 0 0-3.5 3.5C2.5 7 6 11 6 11s3.5-4 3.5-6.5A3.5 3.5 0 0 0 6 1zm0 5a1.4 1.4 0 1 1 0-2.8A1.4 1.4 0 0 1 6 6z"/></svg>
          <span>Your address line 1<br>Your address line 2</span>
        </li>
      </ul>
    </div>
  </section>

  <section class="card card-back" aria-label="Business card back">
    <p class="brand-name"><span class="line-1">Harbourline</span><span class="line-2">Holdings</span></p>
  </section>
</body>
</html>
```